New Fresh design for online Rabbit Game

Hi,

we are a french company working on a online rabbits game for kids, and not kids.

Our website is www.zorvelo.fr, but you can look at the US version : www.quintamble.com

We buy our actual design 2 years ago, but we now think it's too boring and washed out...

We need yours talent to make a really more exacting, more colorful, fresh and dynamic design.

In our game, players have to breed and train rabbits and to make them run races. Players run again friends or players.

Players are kids, between 8 and 15 years. But best players are often parents of these kids !

Our ambiance is clearly funny. We really like if color theme or background look like a nice blue sky, and / or beach. Something that make people happy to come, and say "You are here on holly days to have fun !"

I think the best is if we have 2 layouts, one for the Home page, and one for all other page.

For home page, we are really open to any proposition, we just need to keep our features :
- registration (with rabbit preview)
- connection
- game preview (images slide with small text)
- live race preview (as we have actually)

For other pages layout, we need a layout with a standard container (maybe 850 px width?), and our 2 navigation's bar.

We only need psd, no html integration.

Thanks for your help, please ask me for any questions.
Updates

Hi, 

I have just added some information, concerning layout.

Also we have just committed the budget.

Target Market(s)

Mostly kids between 8 and 15 years.

Industry/Entity Type

It Company

Requirements
Must have
• We already have some characters, like Mr Wimble at the home page and our rabbits. We want to keep all of them, so new design have to match with there style (carton).

If you create an account, you will see we have a big nav bar with 6 tabs, and a little top bar. We absolutely need them to keep a easy navigation in website.

We also need some proposition of element style, like h1, h2, h3, hr, inputs, buttons, notification bubble, etc... So we can work to improve all our pages.
Nice to have
• I think the actual website is a little to wide (about 1000px width). Maybe something like 900px - 850px is more elegant ?
In this case, we can arrange pages to deal with it.

It can be cool if major colors are stil blue and green, to match a little with actual colors. But it's no very important.
Should not have
• We don't want too big header picture (for the all pages layout). I mean, players have to focus on the content.

We don't want photo realistic style, our style is cartoon.

We don't want flash. But Js animations are ok.

```html
<!DOCTYPE html>
<html lang="en">
<head>
<meta charset="utf-8">
<title>Quintamble – Racing and breeding game</title>
<link rel="stylesheet" href="https://fonts.googleapis.com/css2?family=Baloo+2:wght@600;700&family=Ubuntu:wght@400;500;700&display=swap">
<style>
:root{
  --sky-top:#1f8fe0;
  --sky-mid:#6cc0f2;
  --sea:#3aa6d8;
  --sand:#f1e6cf;
  --panel:#ffffff;
  --banner-top:#3bb0ee;
  --banner-bottom:#0f74c4;
  --home:#f2303a;
  --news:#86c712;
  --forum:#f6a200;
  --records:#11b9cc;
  --player:#c8dc2c;
  --player-dark:#a9bf18;
  --link-blue:#1784c7;
  --connect:#a16eaa;
  --connect-dark:#8a5696;
  --overview:#5d87b4;
  --overview-dark:#4a73a0;
  --races:#9ba863;
  --races-dark:#87944f;
  --play-top:#ffc21c;
  --play-bottom:#f19800;
  --footer:#7a4cb6;
  --text-dark:#2b2b2b;
  --white:#ffffff;
  --active-tab:#ffe21a;
}
*{box-sizing:border-box;margin:0;padding:0}
html,body{width:1200px;height:1020px;overflow:hidden}
body{position:relative;font-family:"Ubuntu",sans-serif;color:var(--text-dark)}
.scenery{position:absolute;inset:0;background:linear-gradient(180deg,var(--sky-top) 0%,var(--sky-mid) 45%,#aee0f7 57%,var(--sea) 62%,#7fd0ea 70%,var(--sand) 76%,var(--sand) 100%)}
.palm{position:absolute;left:0;top:270px;width:125px;height:560px;background:linear-gradient(180deg,#5fb33a 0%,#7cbf3d 30%,#b9602a 60%,#8f4820 100%);border-radius:0 60px 40px 0;opacity:.85}
.char{position:absolute;border-radius:40% 40% 30% 30%}
.char-logo-bunny{left:122px;top:32px;width:118px;height:102px;background:radial-gradient(circle at 50% 60%,#d9d0b4,#a89b7a);border-radius:45% 45% 40% 40%}
.brand{position:absolute;left:255px;top:70px;font-family:"Baloo 2",sans-serif;font-weight:700;font-size:32px;color:var(--white);letter-spacing:.3px}
.nav{position:absolute;left:529px;top:71px;display:flex;gap:12px}
.nav a{display:block;height:38px;border:2px solid var(--white);border-radius:8px;font-family:"Baloo 2",sans-serif;font-weight:700;font-size:19px;line-height:38px;color:var(--white);text-decoration:none;text-align:center;letter-spacing:.5px;box-shadow:0 2px 3px rgba(0,0,0,.25)}
.nav .home{width:92px;background:var(--home)}
.nav .news{width:94px;background:var(--news)}
.nav .forum{width:92px;background:var(--forum)}
.nav .records{width:94px;background:var(--records);margin-left:5px}
.grass{position:absolute;left:126px;top:124px;width:950px;height:22px;background:linear-gradient(180deg,#8fd13a,#4f9e1e);border-radius:12px 12px 0 0}
.page{position:absolute;left:120px;top:142px;width:960px;height:748px;background:var(--panel);border-radius:6px;box-shadow:0 2px 6px rgba(0,0,0,.2)}
.banner{position:absolute;left:28px;top:15px;width:906px;height:48px;background:linear-gradient(180deg,var(--banner-top),var(--banner-bottom));border-radius:8px 8px 0 0;text-align:center;font-family:"Ubuntu",sans-serif;font-weight:500;font-size:31px;line-height:46px;color:var(--white);letter-spacing:.6px}
.box{position:absolute;border-radius:6px;color:var(--white)}
.box h2{position:absolute;left:15px;top:10px;font-weight:500;font-size:23px;letter-spacing:.3px}
.box-new{left:10px;top:83px;width:460px;height:250px;background:linear-gradient(180deg,#d6e640,var(--player));border-bottom:4px solid var(--player-dark)}
.box-new h2{color:var(--text-dark)}
.step{position:absolute;font-size:15px;color:var(--link-blue);font-weight:500}
.note{position:absolute;left:252px;top:12px;font-size:14px;font-weight:500;color:var(--text-dark);line-height:18px}
.bunny-name{position:absolute;left:14px;top:82px;font-size:16px;color:#6b6b3a}
.pen{position:absolute;left:58px;top:86px}
.bunny-preview{position:absolute;left:16px;top:126px;width:72px;height:74px;background:radial-gradient(circle,#efeadb,#b7ac92);border-radius:40%}
.picker{position:absolute;left:112px;top:128px;width:118px}
.picker .row{display:flex;align-items:center;justify-content:space-between;height:29px;font-size:14px;color:var(--text-dark)}
.text-field{position:absolute;background:linear-gradient(180deg,#f2f2f2,#ffffff);border-radius:3px;border:none}
.btn-play{position:absolute;width:86px;height:40px;background:linear-gradient(180deg,var(--play-top),var(--play-bottom));border:1px solid #d08300;border-radius:3px;font-family:"Ubuntu",sans-serif;font-weight:500;font-size:17px;color:var(--white);text-align:center;line-height:38px;letter-spacing:.8px}
.box-connect{left:490px;top:83px;width:460px;height:250px;background:var(--connect);border-bottom:4px solid var(--connect-dark)}
.label{position:absolute;left:25px;font-size:13px;color:var(--white)}
.forgot{position:absolute;left:70px;top:146px;font-size:13px;color:var(--text-dark)}
.help{position:absolute;left:26px;top:144px}
.char-wimble{left:905px;top:228px;width:175px;height:248px;background:radial-gradient(circle at 50% 55%,#8fc34d,#4f7d2a);border-radius:45% 45% 30% 30%}
.box-overview{left:10px;top:352px;width:460px;height:382px;background:linear-gradient(180deg,var(--overview),#5a80ab);border-bottom:4px solid var(--overview-dark)}
.tabs{position:absolute;left:37px;top:56px;display:flex;gap:16px;font-size:15px;font-weight:500}
.tabs .current{color:var(--active-tab)}
.shot-pen{position:absolute;left:12px;top:86px;width:435px;height:238px;border:2px solid var(--white);background:linear-gradient(180deg,#5eb944 0%,#4ea738 75%,#e9e2c4 78%,#e9e2c4 100%)}
.caption{position:absolute;left:0;top:337px;width:460px;text-align:center;font-size:12.5px;line-height:16px}
.box-races{left:490px;top:352px;width:460px;height:382px;background:var(--races);border-bottom:4px solid var(--races-dark)}
.race-view{position:absolute;left:18px;top:66px;width:424px;height:280px;border:2px solid var(--white);background:linear-gradient(180deg,#2e1e10 0%,#3a2b1c 18%,#2a2a2a 20%,#4a3a2a 60%,#2f2016 100%)}
.race-pitch{position:absolute;left:20px;top:100px;font-family:"Ubuntu",sans-serif;font-weight:500;font-size:28px;line-height:36px;color:var(--white);text-align:center;width:420px;text-shadow:0 1px 2px rgba(0,0,0,.6)}
.char-boar{left:975px;top:668px;width:200px;height:222px;background:radial-gradient(circle at 50% 45%,#8b7a4a,#3b3524);border-radius:45% 45% 25% 25%}
.footer-bar{position:absolute;left:120px;top:907px;width:960px;height:63px;background:var(--footer);border:2px solid var(--white);border-radius:4px;color:var(--white);font-size:12.5px;font-weight:500}
.partners{position:absolute;left:22px;top:23px}
.partner-badge{position:absolute;left:90px;top:14px;width:88px;height:30px;background:#1b3f8f;border:1px solid #c9d4ea}
.footer-links{position:absolute;right:14px;top:23px}
.copyright{position:absolute;left:0;top:987px;width:1200px;text-align:center;font-size:12.5px;font-weight:500;color:#4a4a4a}
</style>
</head>
<body>
<div class="scenery" role="img" aria-label="Cartoon blue sky with clouds over a sunny beach and sea"></div>
<div class="palm" role="img" aria-label="Cartoon palm tree with coconuts"></div>

<header>
  <div class="char char-logo-bunny" role="img" aria-label="Cartoon bunny mascot"></div>
  <div class="brand">Quintamble</div>
  <nav class="nav">
    <a class="home" href="#">HOME</a>
    <a class="news" href="#">NEWS</a>
    <a class="forum" href="#">FORUM</a>
    <a class="records" href="#">RECORDS</a>
  </nav>
  <div class="grass" role="img" aria-label="Grass strip with daisies"></div>
</header>

<main class="page">
  <h1 class="banner">The coolest racing and breeding game there is</h1>

  <section class="box box-new">
    <h2>New player</h2>
    <p class="note">Register in just a couple<br>of seconds!</p>
    <p class="step" style="left:14px;top:52px">1 - Choose your bunny</p>
    <p class="step" style="left:250px;top:52px">2 - Choose a username</p>
    <p class="bunny-name">Zoey</p>
    <svg class="pen" width="22" height="16" viewBox="0 0 22 16"><path d="M2 12 L14 2 L19 6 L7 16 Z" fill="#34507a"/><path d="M2 12 L0 16 L7 16 Z" fill="#c9a46a"/></svg>
    <div class="bunny-preview" role="img" aria-label="Preview of the chosen grey bunny"></div>
    <div class="picker">
      <div class="row"><svg width="14" height="18"><path d="M12 1 L2 9 L12 17 Z" fill="#eee" stroke="#999"/></svg>Original<svg width="14" height="18"><path d="M2 1 L12 9 L2 17 Z" fill="#eee" stroke="#999"/></svg></div>
      <div class="row"><svg width="14" height="18"><path d="M12 1 L2 9 L12 17 Z" fill="#eee" stroke="#999"/></svg>Gray<svg width="14" height="18"><path d="M2 1 L12 9 L2 17 Z" fill="#eee" stroke="#999"/></svg></div>
      <div class="row"><svg width="14" height="18"><path d="M12 1 L2 9 L12 17 Z" fill="#eee" stroke="#999"/></svg>Male<svg width="14" height="18"><path d="M2 1 L12 9 L2 17 Z" fill="#eee" stroke="#999"/></svg></div>
    </div>
    <input class="text-field" style="left:274px;top:82px;width:160px;height:28px" type="text" aria-label="Username">
    <p class="step" style="left:250px;top:134px">3 - OK! We're good to go!</p>
    <div class="btn-play" style="left:300px;top:170px">PLAY</div>
  </section>

  <section class="box box-connect">
    <h2>Connexion</h2>
    <span class="label" style="top:54px">Username:</span>
    <input class="text-field" style="left:109px;top:48px;width:160px;height:28px" type="text" aria-label="Username">
    <span class="label" style="top:99px">Password:</span>
    <input class="text-field" style="left:109px;top:92px;width:160px;height:28px" type="password" aria-label="Password">
    <svg class="help" width="22" height="22" viewBox="0 0 22 22"><circle cx="11" cy="11" r="9.5" fill="#2a73c2" stroke="#fff" stroke-width="2"/><text x="11" y="15.5" text-anchor="middle" font-family="Ubuntu,sans-serif" font-size="13" font-weight="700" fill="#fff">?</text></svg>
    <span class="forgot">Forgot password?</span>
    <div class="btn-play" style="left:184px;top:135px">PLAY</div>
  </section>

  <section class="box box-overview">
    <h2>Game overview</h2>
    <div class="tabs"><span class="current">Your Pen</span><span>Your Allotment</span><span>Professions</span><span>Universe</span></div>
    <div class="shot-pen" role="img" aria-label="Game screen of a bunny pen with bunnies playing on the grass"></div>
    <p class="caption">Breed, educate and train your bunnies in your pen. Watch as they play<br>and grow up together <strong>under your very eyes!</strong></p>
  </section>

  <section class="box box-races">
    <h2>Take part in races with other players</h2>
    <div class="race-view" role="img" aria-label="Live bunny race on a track with spectators"></div>
    <p class="race-pitch">Come and train your bunnies<br>and challenge your friends</p>
  </section>
</main>

<div class="char char-wimble" role="img" aria-label="Mr Wimble, the turtle race coach with a cap and stopwatch"></div>
<div class="char char-boar" role="img" aria-label="Cartoon boar character leaning on a shovel"></div>

<footer>
  <div class="footer-bar">
    <span class="partners">Partners :</span>
    <div class="partner-badge" role="img" aria-label="Partner listing badge"></div>
    <span class="footer-links">Rules - General Terms and Conditions - Contact - Quintamble.com 3.0</span>
  </div>
  <p class="copyright">Copyright ©2012 All Right Reserved &nbsp;/&nbsp; Privacy Policy</p>
</footer>
</body>
</html>
```